TA BRAMLEY BUSINESS CARD DESIGN PROJECT

We need to utilize our logo that was expertly created on PixelHarbor and now need to match this with a business card design.

```html
<!DOCTYPE html>
<html lang="en">
<head>
<meta charset="utf-8">
<title>TA Bramley Business Card</title>
<link href="https://fonts.googleapis.com/css2?family=Open+Sans:wght@400;600;700&display=swap" rel="stylesheet">
<style>
  :root {
    --backdrop: #3b3b3b;
    --card: #151515;
    --brand-blue: #1b5cc8;
    --ink-light: #e6e6e6;
    --ink-muted: #5a5a5a;
    --divider: #1f3f73;
  }
  * { margin: 0; padding: 0; box-sizing: border-box; }
  html, body {
    width: 1200px; height: 801px; overflow: hidden;
    background: var(--backdrop);
    font-family: "Open Sans", Arial, sans-serif;
  }
  .stage {
    position: relative; width: 1200px; height: 801px;
    display: flex; align-items: center; justify-content: center; gap: 40px;
  }
  .card {
    position: relative; width: 520px; height: 300px;
    background: var(--card);
    border-bottom: 3px solid var(--brand-blue);
    border-right: 1px solid var(--brand-blue);
  }
  .card-front .identity {
    position: absolute; left: 44px; top: 60px; width: 240px;
  }
  .brand-name {
    color: var(--brand-blue); font-weight: 700; font-size: 34px;
    letter-spacing: 3px; line-height: 1.1;
  }
  .brand-name .mark {
    display: inline-block; width: 18px; height: 18px;
    background: var(--brand-blue); margin-right: 10px; vertical-align: middle;
  }
  .person { position: absolute; left: 44px; bottom: 56px; }
  .person-name {
    color: var(--brand-blue); font-weight: 700; font-size: 19px; letter-spacing: 0.5px;
  }
  .person-title { color: var(--ink-light); font-size: 14px; margin-top: 2px; }
  .divider {
    position: absolute; left: 300px; top: 110px; width: 1px; height: 80px;
    background: var(--divider);
  }
  .contacts {
    position: absolute; left: 322px; top: 108px; list-style: none;
    color: var(--ink-light); font-size: 13px; line-height: 28px;
  }
  .contacts li { display: flex; align-items: center; gap: 8px; }
  .contacts svg { width: 12px; height: 12px; fill: var(--brand-blue); }
  .card-back { display: flex; align-items: center; justify-content: center; }
  .back-name {
    color: var(--ink-muted); font-weight: 700; font-size: 40px; letter-spacing: 4px;
  }
</style>
</head>
<body>
<main class="stage">
  <section class="card card-front">
    <div class="identity">
      <div class="brand-name"><span class="mark"></span>TA BRAMLEY</div>
    </div>
    <div class="person">
      <div class="person-name">DORIAN VALE</div>
      <div class="person-title">President</div>
    </div>
    <div class="divider"></div>
    <ul class="contacts">
      <li><svg viewBox="0 0 12 12"><path d="M2.5 1h2l1 3-1.5 1a6 6 0 0 0 3 3l1-1.5 3 1v2a1.5 1.5 0 0 1-1.5 1.5A9.5 9.5 0 0 1 1 2.5 1.5 1.5 0 0 1 2.5 1z"/></svg>555-013-0742</li>
      <li><svg viewBox="0 0 12 12"><path d="M1 2.5h10v7H1z M1 2.5l5 4 5-4" stroke="#151515" stroke-width="0.8"/></svg>d.vale@tabramley.com</li>
      <li><svg viewBox="0 0 12 12"><circle cx="6" cy="6" r="5"/></svg>www.tabramley.com</li>
    </ul>
  </section>
  <section class="card card-back">
    <div class="back-name">TA BRAMLEY</div>
  </section>
</main>
</body>
</html>
```